Card Design for my dog training business Brightpaw Obedience

Need a business card design for my dog training business with my new logo. Want the card to come off professional yet fun. Want it to be very eye catchy as well. I normally have these at vet clinics, pet stores, and groomers. so need it to look better than my competitors.
Target Market(s)
dog owners
Industry/Entity Type
Dog Training
Contact Information for Business Card
needs logo, my name and info
Font styles to use
Serif
Colors
0255a3
ffffff
ec1f27
000000
333333
fbfbfb
Requirements
Must have
- Brightpaw Obedience
- Felix Orland
- 415 903 2276
- info@brightpawobedience.example
- www.brightpawobedience.example

```html
<!DOCTYPE html>
<html lang="en">
<head>
<meta charset="utf-8">
<title>Brightpaw Obedience – Business Card</title>
<link href="https://fonts.googleapis.com/css2?family=EB+Garamond:ital,wght@0,400;1,400&family=Montserrat:wght@400;500&display=swap" rel="stylesheet">
<style>
  :root {
    --backdrop: #1a1a1a;
    --card-light: #e6e6e6;
    --band-dark: #231f20;
    --ink-black: #000000;
    --back-card: #1e1e1f;
    --silver: #a9a9a9;
    --text-light: #ffffff;
    --text-muted: #d6d6d6;
    --ink-dark: #1a1a1a;
  }
  * { margin: 0; padding: 0; box-sizing: border-box; }
  html, body { width: 1200px; height: 1200px; overflow: hidden; background: var(--backdrop); }
  .canvas { position: relative; width: 1200px; height: 1200px; }

  .card { position: absolute; left: 227px; width: 745px; height: 424px; overflow: hidden; }
  .card-front { top: 136px; background: var(--card-light); }
  .card-back { top: 640px; background: var(--back-card); }

  .brand-name {
    position: absolute; left: 37px; top: 48px;
    font-family: "EB Garamond", serif; font-weight: 400; font-size: 46px;
    color: var(--ink-dark); line-height: 1.1; width: 300px;
  }

  .contact-band { position: absolute; left: 0; top: 202px; width: 745px; height: 188px; background: var(--band-dark); }
  .accent-block { position: absolute; left: 581px; top: 202px; width: 164px; height: 164px; background: var(--ink-black); }
  .dog-illustration {
    position: absolute; left: 409px; top: 156px; width: 284px; height: 236px;
    background: linear-gradient(160deg, #eeeeee, #c9c9c9);
    border-radius: 40px 60px 30px 50px;
  }

  .person { position: absolute; left: 36px; top: 226px; font-family: "Montserrat", sans-serif; }
  .person-name { font-size: 21px; font-weight: 500; letter-spacing: 1px; color: var(--text-light); text-transform: uppercase; }
  .person-role { font-size: 16px; font-weight: 400; color: var(--text-muted); margin-top: 4px; }

  .contact-list { position: absolute; left: 36px; top: 296px; list-style: none; font-family: "Montserrat", sans-serif; font-size: 16px; color: var(--text-muted); }
  .contact-list li { display: flex; align-items: center; height: 24px; }
  .contact-list svg { width: 15px; height: 15px; margin-right: 9px; flex-shrink: 0; }

  .back-emblem {
    position: absolute; left: 251px; top: 76px; width: 236px; height: 160px;
    background: linear-gradient(160deg, #4a4a4a, #2e2e2e);
    border-radius: 12px;
  }
  .back-brand {
    position: absolute; left: 0; width: 100%; top: 248px; text-align: center;
    font-family: "EB Garamond", serif; font-weight: 400; font-size: 36px; color: var(--silver);
  }
  .tagline {
    position: absolute; left: 0; width: 100%; top: 330px; text-align: center;
    font-family: "EB Garamond", serif; font-style: italic; font-size: 13px; color: var(--silver);
  }
</style>
</head>
<body>
<main class="canvas">
  <section class="card card-front">
    <div class="brand-name">Brightpaw Obedience</div>
    <div class="contact-band"></div>
    <div class="accent-block"></div>
    <div class="dog-illustration" role="img" aria-label="Line-drawn portraits of two dogs, a shepherd and a doberman, in black and white"></div>

    <div class="person">
      <div class="person-name">Felix Orland</div>
      <div class="person-role">Managing Director</div>
    </div>

    <ul class="contact-list">
      <li>
        <svg viewBox="0 0 16 16" aria-hidden="true"><circle cx="8" cy="8" r="8" fill="#d6d6d6"/><path d="M5 5.5c1-1 2-1 2.3 0l.4 1-1 .8c.4 1 1 1.6 2 2l.8-1 1 .4c1 .3 1 1.3 0 2.3-2.5 1-6.5-3-5.5-5.5z" fill="#231f20"/></svg>
        415 903 2276
      </li>
      <li>
        <svg viewBox="0 0 16 16" aria-hidden="true"><circle cx="8" cy="8" r="8" fill="#d6d6d6"/><rect x="4" y="5.2" width="8" height="5.6" fill="none" stroke="#231f20" stroke-width="1"/><path d="M4 5.4l4 3 4-3" fill="none" stroke="#231f20" stroke-width="1"/></svg>
        info@brightpawobedience.example
      </li>
      <li>
        <svg viewBox="0 0 16 16" aria-hidden="true"><circle cx="8" cy="8" r="8" fill="#d6d6d6"/><circle cx="8" cy="8" r="4.5" fill="none" stroke="#231f20" stroke-width="1"/><path d="M3.5 8h9M8 3.5c-2 2.5-2 6.5 0 9M8 3.5c2 2.5 2 6.5 0 9" fill="none" stroke="#231f20" stroke-width="0.8"/></svg>
        www.brightpawobedience.example
      </li>
    </ul>
  </section>

  <section class="card card-back">
    <div class="back-emblem" role="img" aria-label="Silver outline of a state map framing line drawings of two dogs"></div>
    <div class="back-brand">Brightpaw Obedience</div>
    <p class="tagline">“Good habits for happy dogs, one lesson at a time.”</p>
  </section>
</main>
</body>
</html>
```